iPhone iOS 7 App For Managing Tasks/Photos for Internal Company Use

We need an app design that displays company objectives and task, and provides the interface for employees to complete a task by uploading a photo and adding comments.

Please see attached mock up sketches as a rough guideline

Final delivery of files must contain PSD, and all layers/objects sliced both is PSD and PNG files

Target Market(s)

This is a tool for internal employee use

Industry/Entity Type

It Company

Requirements
Must have
• Must include logo, and match the colour scheme
Use iPhone iOS 7 Style

```html
<!DOCTYPE html>
<html lang="en">
<head>
<meta charset="utf-8">
<title>Tasks</title>
<link rel="stylesheet" href="https://fonts.googleapis.com/css2?family=Roboto:wght@400;500&display=swap">
<style>
  :root {
    --bg: #efeff4;
    --bar: #f7f7f7;
    --line: #d4d4d8;
    --text: #111111;
    --chevron: #b0b4ba;
    --row: #ffffff;
    --row-tint: #e6ebef;
    --tab: #3e5f63;
    --tab-icon: #e8eeef;
    --badge: #e8402c;
    --back: #7a7a80;
  }
  * { margin: 0; padding: 0; box-sizing: border-box; }
  html, body { width: 677px; height: 1200px; overflow: hidden; }
  body {
    background: var(--bg);
    font-family: "Helvetica Neue", "Roboto", Arial, sans-serif;
    color: var(--text);
    position: relative;
  }
  .status-bar {
    position: absolute; top: 0; left: 0; right: 0; height: 42px;
    background: var(--bar);
    display: flex; align-items: center; justify-content: space-between;
    padding: 0 12px; font-size: 24px;
  }
  .status-left { display: flex; align-items: center; gap: 8px; }
  .signal { display: flex; gap: 3px; }
  .signal span { width: 10px; height: 10px; border-radius: 50%; background: #222; }
  .signal span.off { background: none; border: 1.5px solid #222; }
  .status-time { position: absolute; left: 0; right: 0; text-align: center; font-weight: 500; pointer-events: none; }
  .status-right { display: flex; align-items: center; gap: 8px; }
  .nav-bar {
    position: absolute; top: 42px; left: 0; right: 0; height: 94px;
    background: var(--bar); border-bottom: 1px solid var(--line);
    display: flex; align-items: center; font-size: 38px;
  }
  .back { display: flex; align-items: center; gap: 12px; padding-left: 18px; color: var(--text); }
  .nav-title { margin-left: 62px; }
  .task-list { list-style: none; position: absolute; left: 0; right: 0; top: 0; }
  .task {
    position: absolute; left: 0; right: 0; height: 92px;
    background: var(--row);
    border-top: 1px solid var(--line); border-bottom: 1px solid var(--line);
    display: flex; align-items: center; justify-content: space-between;
    padding: 0 24px 0 26px; font-size: 31px;
  }
  .task.highlight { background: linear-gradient(90deg, var(--row) 0%, var(--row) 20%, var(--row-tint) 100%); }
  .tab-bar {
    position: absolute; left: 0; right: 0; bottom: 0; height: 108px;
    background: var(--tab);
    display: flex; align-items: center; justify-content: space-around; padding: 0 30px;
  }
  .tab-item { position: relative; width: 60px; height: 60px; display: flex; align-items: center; justify-content: center; }
  .badge { position: absolute; top: 2px; right: 2px; width: 16px; height: 16px; border-radius: 50%; background: var(--badge); }
</style>
</head>
<body>
  <header class="status-bar">
    <div class="status-left">
      <div class="signal"><span></span><span></span><span></span><span class="off"></span><span class="off"></span></div>
      <span>NOVA</span>
      <svg width="26" height="20" viewBox="0 0 26 20"><path d="M13 19 L1 6 A17 17 0 0 1 25 6 Z" fill="#222"/></svg>
    </div>
    <div class="status-time">4:21 PM</div>
    <div class="status-right">
      <span>22%</span>
      <svg width="46" height="22" viewBox="0 0 46 22"><rect x="1" y="1" width="40" height="20" rx="3" fill="none" stroke="#222" stroke-width="2"/><rect x="4" y="4" width="9" height="14" fill="#222"/><rect x="42" y="7" width="3" height="8" fill="#222"/></svg>
    </div>
  </header>

  <nav class="nav-bar">
    <div class="back">
      <svg width="16" height="28" viewBox="0 0 16 28"><path d="M13 3 L3 14 L13 25" fill="none" stroke="var(--back)" stroke-width="3"/></svg>
      <span>Objectives</span>
    </div>
    <span class="nav-title">Tasks</span>
  </nav>

  <ul class="task-list">
    <li class="task highlight" style="top:241px">Task 1<svg width="14" height="26" viewBox="0 0 14 26"><path d="M2 2 L12 13 L2 24" fill="none" stroke="var(--chevron)" stroke-width="3"/></svg></li>
    <li class="task highlight" style="top:368px">Task 2<svg width="14" height="26" viewBox="0 0 14 26"><path d="M2 2 L12 13 L2 24" fill="none" stroke="var(--chevron)" stroke-width="3"/></svg></li>
    <li class="task" style="top:501px">Task 3<svg width="14" height="26" viewBox="0 0 14 26"><path d="M2 2 L12 13 L2 24" fill="none" stroke="var(--chevron)" stroke-width="3"/></svg></li>
    <li class="task" style="top:634px">Task 4<svg width="14" height="26" viewBox="0 0 14 26"><path d="M2 2 L12 13 L2 24" fill="none" stroke="var(--chevron)" stroke-width="3"/></svg></li>
    <li class="task" style="top:767px">Task 5<svg width="14" height="26" viewBox="0 0 14 26"><path d="M2 2 L12 13 L2 24" fill="none" stroke="var(--chevron)" stroke-width="3"/></svg></li>
  </ul>

  <footer class="tab-bar">
    <div class="tab-item">
      <svg width="46" height="42" viewBox="0 0 46 42"><path d="M23 2 L2 22 H8 V40 H19 V28 H27 V40 H38 V22 H44 Z" fill="var(--tab-icon)"/></svg>
    </div>
    <div class="tab-item">
      <svg width="46" height="46" viewBox="0 0 46 46"><circle cx="23" cy="23" r="21" fill="var(--tab-icon)"/><path d="M23 23 V2 A21 21 0 0 1 44 23 Z" fill="var(--tab)"/><path d="M26 20 V6 A17 17 0 0 1 40 20 Z" fill="var(--tab-icon)"/></svg>
    </div>
    <div class="tab-item">
      <svg width="48" height="44" viewBox="0 0 48 44"><path d="M4 6 H40 V30 H16 L6 39 V30 H4 Z" fill="var(--tab-icon)"/><rect x="10" y="12" width="24" height="3" fill="var(--tab)"/><rect x="10" y="19" width="20" height="3" fill="var(--tab)"/></svg>
      <span class="badge"></span>
    </div>
    <div class="tab-item">
      <svg width="44" height="42" viewBox="0 0 44 42"><path d="M4 2 H30 V14 H26 V6 H8 V36 H26 V28 H30 V40 H4 Z" fill="var(--tab-icon)"/><path d="M14 18 H30 V11 L42 21 L30 31 V24 H14 Z" fill="var(--tab-icon)"/></svg>
    </div>
  </footer>
</body>
</html>
```